Fun A1 2012 family planner using clever typography and block colour

I have been looking for an A1 2012 family planner and I have not been able to find one. Hence I would like help to develop such a planner. I plan to print it on matt paper, portrait orientated. I have attached some reference pictures of our 2011 planner. I like interesting typography, clear clean colours and simple illustration. I need space to write in daily events and need the weeks and days to be clearly delineated from each other. Each day cell needs the date and day in it (please refer to the file uploaded for a visual reference confirming this). Each weekend needs some kind of colour/ typographic delineation. I want a design for a year-at-a-view calendar. I plan to print the planner in Sydney, Australia with brightloomprints.com.au and probably to sell printed copies online. The terms & conditions of this project are that I will own the design concept 100% and in perpetuity worldwide once payment has been made. (NB. The attached Work File in Word contains a rough layout and all months, days and dates all typed up to make for quicker design.)

Target Market(s)

Reasonably well heeled family of 4. 2 parents. 2 kids. 2 pets.

Industry/Entity Type

Events

Requirements
Must have
• The calendar must be portrait (not landscape orientated), A1 size. It will be printed on matt paper by brightloomprints.com.au. It must have months running left to right (Jan-Dec) and day/date cells running top to bottom (refer 2011 planner photos in file uploaded). The day/ date cells must be around 3(w)x2(h)cm - big enough to write daily events in. Weekends must be colour/ typographically delineated. 2012 year must be noted as must "A Pebblegate Inc Project" and web address in fine print bottom left hand left hand corner.
Nice to have
• A Pebblegate Inc logo in bottom left hand corder (perhaps Nimble Owl like: http://www.artmarketly.com/design_submission.aspx?designid=731462). Header/Footer space for customisation (e.g. "Hartono-Quist 2012 Planner" or "XYZ Co 2012 Planner".
Should not have
• The calendar should not use photographs or resemble standard or cheesy wall calendars. No watermarks please.

```html
<!DOCTYPE html>
<html lang="en">
<head>
<meta charset="utf-8">
<title>XYZ Co 2012 Planner</title>
<link rel="stylesheet" href="https://fonts.googleapis.com/css2?family=Fredoka:wght@600;700&family=Nunito:wght@600;800&display=swap">
<style>
:root{
  --paper:#ffffff;
  --num:#5a5a5a;
  --day:#7a7a7a;
  --footer:#dedede;
  --orange:#f7941d; --yellow:#fff27a; --yellow-line:#fbf0b4;
  --cyan:#00aeef; --cyan-ink:#0b96d6; --sky:#a9dcf5; --sky-line:#cfeaf8;
  --pink:#f26ba6; --pink-ink:#e94a92; --blush:#f6b7d3; --blush-line:#f9d3e4;
  --red:#ed1c24; --peach:#fcc49a; --peach-line:#fcdcc3;
  --green:#8dc63f; --green-ink:#6aab2d; --mint:#d6e9c1; --mint-line:#e3efd4;
  --purple:#8e4fa1; --purple-ink:#8c4c9c; --lilac:#d9c1de; --lilac-line:#e8daec;
}
*{margin:0;padding:0;box-sizing:border-box}
html,body{width:847px;height:1200px;overflow:hidden;background:var(--paper)}
.poster{position:relative;width:847px;height:1200px}
.planner{position:absolute;left:30px;top:20px;display:flex;gap:2.2px}
.month{width:64px;display:flex;flex-direction:column;gap:1.8px}
.month h2{height:84px;margin-bottom:2px;font:700 34px/1 "Fredoka",sans-serif;writing-mode:vertical-rl;color:var(--ink);letter-spacing:-1px;align-self:center;text-align:center}
.day{height:32px;border:1px solid var(--line);border-radius:4px;padding:2px 0 0 4px;font:800 14px/1 "Nunito",sans-serif;color:var(--num)}
.day i{display:block;font:600 7px/1.2 "Nunito",sans-serif;font-style:normal;color:var(--day)}
.day.weekend{background:var(--fill);border-color:var(--fill);color:var(--accent)}
.day.weekend i{color:var(--accent)}
.jan,.jul{--ink:var(--orange);--fill:var(--yellow);--line:var(--yellow-line);--accent:var(--orange)}
.feb,.aug{--ink:var(--cyan);--fill:var(--sky);--line:var(--sky-line);--accent:var(--cyan-ink)}
.mar,.sep{--ink:var(--pink);--fill:var(--blush);--line:var(--blush-line);--accent:var(--pink-ink)}
.apr,.oct{--ink:var(--red);--fill:var(--peach);--line:var(--peach-line);--accent:var(--red)}
.may,.nov{--ink:var(--green);--fill:var(--mint);--line:var(--mint-line);--accent:var(--green-ink)}
.jun,.dec{--ink:var(--purple);--fill:var(--lilac);--line:var(--lilac-line);--accent:var(--purple-ink)}
.title{position:absolute;left:30px;top:1162px;font:600 27px/1 "Fredoka",sans-serif;color:var(--footer);letter-spacing:.5px}
</style>
</head>
<body>
<main class="poster">
<div class="planner">

<section class="month jan"><h2>JAN</h2>
<p class="day weekend">01<i>Sun</i></p><p class="day">02<i>Mon</i></p><p class="day">03<i>Tue</i></p><p class="day">02<i>Thu</i></p><p class="day">05<i>Thu</i></p><p class="day">06<i>Fri</i></p><p class="day weekend">07<i>Sat</i></p>
<p class="day weekend">08<i>Sun</i></p><p class="day">09<i>Mon</i></p><p class="day">10<i>Tue</i></p><p class="day">02<i>Thu</i></p><p class="day">12<i>Thu</i></p><p class="day">13<i>Fri</i></p><p class="day weekend">14<i>Sat</i></p>
<p class="day weekend">15<i>Sun</i></p><p class="day">16<i>Mon</i></p><p class="day">17<i>Tue</i></p><p class="day">02<i>Thu</i></p><p class="day">19<i>Thu</i></p><p class="day">20<i>Fri</i></p><p class="day weekend">21<i>Sat</i></p>
<p class="day weekend">22<i>Sun</i></p><p class="day">23<i>Mon</i></p><p class="day">24<i>Tue</i></p><p class="day">02<i>Thu</i></p><p class="day">26<i>Thu</i></p><p class="day">27<i>Fri</i></p><p class="day weekend">28<i>Sat</i></p>
<p class="day weekend">29<i>Sun</i></p><p class="day">30<i>Mon</i></p><p class="day">31<i>Tue</i></p>
</section>

<section class="month feb"><h2>FEB</h2>
<p class="day">01<i>Wed</i></p><p class="day">02<i>Thu</i></p><p class="day">01<i>Wed</i></p><p class="day weekend">02<i>Thu</i></p><p class="day weekend">01<i>Wed</i></p><p class="day">02<i>Thu</i></p><p class="day">01<i>Wed</i></p>
<p class="day">01<i>Wed</i></p><p class="day">02<i>Thu</i></p><p class="day">01<i>Wed</i></p><p class="day weekend">02<i>Thu</i></p><p class="day weekend">01<i>Wed</i></p><p class="day">02<i>Thu</i></p><p class="day">01<i>Wed</i></p>
<p class="day">01<i>Wed</i></p><p class="day">02<i>Thu</i></p><p class="day">01<i>Wed</i></p><p class="day weekend">02<i>Thu</i></p><p class="day weekend">01<i>Wed</i></p><p class="day">02<i>Thu</i></p><p class="day">01<i>Wed</i></p>
<p class="day">01<i>Wed</i></p><p class="day">02<i>Thu</i></p><p class="day">01<i>Wed</i></p><p class="day weekend">02<i>Thu</i></p><p class="day weekend">01<i>Wed</i></p><p class="day">02<i>Thu</i></p><p class="day">01<i>Wed</i></p>
<p class="day">01<i>Wed</i></p><p class="day">02<i>Thu</i></p><p class="day">01<i>Wed</i></p>
</section>

<section class="month mar"><h2>MAR</h2>
<p class="day">01<i>Thu</i></p><p class="day">02<i>Fri</i></p><p class="day weekend">01<i>Thu</i></p><p class="day weekend">02<i>Fri</i></p><p class="day">01<i>Thu</i></p><p class="day">02<i>Fri</i></p><p class="day">01<i>Thu</i></p>
<p class="day">01<i>Thu</i></p><p class="day">02<i>Fri</i></p><p class="day weekend">01<i>Thu</i></p><p class="day weekend">02<i>Fri</i></p><p class="day">01<i>Thu</i></p><p class="day">02<i>Fri</i></p><p class="day">01<i>Thu</i></p>
<p class="day">01<i>Thu</i></p><p class="day">02<i>Fri</i></p><p class="day weekend">01<i>Thu</i></p><p class="day weekend">02<i>Fri</i></p><p class="day">01<i>Thu</i></p><p class="day">02<i>Fri</i></p><p class="day">01<i>Thu</i></p>
<p class="day">01<i>Thu</i></p><p class="day">02<i>Fri</i></p><p class="day weekend">01<i>Thu</i></p><p class="day weekend">02<i>Fri</i></p><p class="day">01<i>Thu</i></p><p class="day">02<i>Fri</i></p><p class="day">01<i>Thu</i></p>
<p class="day">01<i>Thu</i></p><p class="day">02<i>Fri</i></p><p class="day weekend">01<i>Thu</i></p>
</section>

<section class="month apr"><h2>APR</h2>
<p class="day weekend">01<i>Sun</i></p><p class="day">02<i>Mon</i></p><p class="day">01<i>Sun</i></p><p class="day">02<i>Mon</i></p><p class="day">01<i>Sun</i></p><p class="day">02<i>Mon</i></p><p class="day weekend">01<i>Sun</i></p>
<p class="day weekend">01<i>Sun</i></p><p class="day">02<i>Mon</i></p><p class="day">01<i>Sun</i></p><p class="day">02<i>Mon</i></p><p class="day">01<i>Sun</i></p><p class="day">02<i>Mon</i></p><p class="day weekend">01<i>Sun</i></p>
<p class="day weekend">01<i>Sun</i></p><p class="day">02<i>Mon</i></p><p class="day">01<i>Sun</i></p><p class="day">02<i>Mon</i></p><p class="day">01<i>Sun</i></p><p class="day">02<i>Mon</i></p><p class="day weekend">01<i>Sun</i></p>
<p class="day weekend">01<i>Sun</i></p><p class="day">02<i>Mon</i></p><p class="day">01<i>Sun</i></p><p class="day">02<i>Mon</i></p><p class="day">01<i>Sun</i></p><p class="day">02<i>Mon</i></p><p class="day weekend">01<i>Sun</i></p>
<p class="day weekend">01<i>Sun</i></p><p class="day">02<i>Mon</i></p><p class="day">01<i>Sun</i></p>
</section>

<section class="month may"><h2>MAY</h2>
<p class="day">01<i>Tue</i></p><p class="day">02<i>Wed</i></p><p class="day">01<i>Tue</i></p><p class="day">02<i>Wed</i></p><p class="day weekend">01<i>Tue</i></p><p class="day weekend">02<i>Wed</i></p><p class="day">01<i>Tue</i></p>
<p class="day">01<i>Tue</i></p><p class="day">02<i>Wed</i></p><p class="day">01<i>Tue</i></p><p class="day">02<i>Wed</i></p><p class="day weekend">01<i>Tue</i></p><p class="day weekend">02<i>Wed</i></p><p class="day">01<i>Tue</i></p>
<p class="day">01<i>Tue</i></p><p class="day">02<i>Wed</i></p><p class="day">01<i>Tue</i></p><p class="day">02<i>Wed</i></p><p class="day weekend">01<i>Tue</i></p><p class="day weekend">02<i>Wed</i></p><p class="day">01<i>Tue</i></p>
<p class="day">01<i>Tue</i></p><p class="day">02<i>Wed</i></p><p class="day">01<i>Tue</i></p><p class="day">02<i>Wed</i></p><p class="day weekend">01<i>Tue</i></p><p class="day weekend">02<i>Wed</i></p><p class="day">01<i>Tue</i></p>
<p class="day">01<i>Tue</i></p><p class="day">02<i>Wed</i></p><p class="day">01<i>Tue</i></p>
</section>

<section class="month jun"><h2>JUN</h2>
<p class="day">01<i>Fri</i></p><p class="day weekend">02<i>Sat</i></p><p class="day weekend">01<i>Fri</i></p><p class="day">02<i>Sat</i></p><p class="day">01<i>Fri</i></p><p class="day">02<i>Sat</i></p><p class="day">01<i>Fri</i></p>
<p class="day">01<i>Fri</i></p><p class="day weekend">02<i>Sat</i></p><p class="day weekend">01<i>Fri</i></p><p class="day">02<i>Sat</i></p><p class="day">01<i>Fri</i></p><p class="day">02<i>Sat</i></p><p class="day">01<i>Fri</i></p>
<p class="day">01<i>Fri</i></p><p class="day weekend">02<i>Sat</i></p><p class="day weekend">01<i>Fri</i></p><p class="day">02<i>Sat</i></p><p class="day">01<i>Fri</i></p><p class="day">02<i>Sat</i></p><p class="day">01<i>Fri</i></p>
<p class="day">01<i>Fri</i></p><p class="day weekend">02<i>Sat</i></p><p class="day weekend">01<i>Fri</i></p><p class="day">02<i>Sat</i></p><p class="day">01<i>Fri</i></p><p class="day">02<i>Sat</i></p><p class="day">01<i>Fri</i></p>
<p class="day">01<i>Fri</i></p><p class="day weekend">02<i>Sat</i></p><p class="day weekend">01<i>Fri</i></p>
</section>

<section class="month jul"><h2>JUL</h2>
<p class="day weekend">01<i>Sun</i></p><p class="day">02<i>Mon</i></p><p class="day">01<i>Sun</i></p><p class="day">02<i>Mon</i></p><p class="day">01<i>Sun</i></p><p class="day">02<i>Mon</i></p><p class="day weekend">01<i>Sun</i></p>
<p class="day weekend">01<i>Sun</i></p><p class="day">02<i>Mon</i></p><p class="day">01<i>Sun</i></p><p class="day">02<i>Mon</i></p><p class="day">01<i>Sun</i></p><p class="day">02<i>Mon</i></p><p class="day weekend">01<i>Sun</i></p>
<p class="day weekend">01<i>Sun</i></p><p class="day">02<i>Mon</i></p><p class="day">01<i>Sun</i></p><p class="day">02<i>Mon</i></p><p class="day">01<i>Sun</i></p><p class="day">02<i>Mon</i></p><p class="day weekend">01<i>Sun</i></p>
<p class="day weekend">01<i>Sun</i></p><p class="day">02<i>Mon</i></p><p class="day">01<i>Sun</i></p><p class="day">02<i>Mon</i></p><p class="day">01<i>Sun</i></p><p class="day">02<i>Mon</i></p><p class="day weekend">01<i>Sun</i></p>
<p class="day weekend">01<i>Sun</i></p><p class="day">02<i>Mon</i></p><p class="day">01<i>Sun</i></p>
</section>

<section class="month aug"><h2>AUG</h2>
<p class="day">01<i>Wed</i></p><p class="day">02<i>Thu</i></p><p class="day">01<i>Wed</i></p><p class="day weekend">02<i>Thu</i></p><p class="day weekend">01<i>Wed</i></p><p class="day">02<i>Thu</i></p><p class="day">01<i>Wed</i></p>
<p class="day">01<i>Wed</i></p><p class="day">02<i>Thu</i></p><p class="day">01<i>Wed</i></p><p class="day weekend">02<i>Thu</i></p><p class="day weekend">01<i>Wed</i></p><p class="day">02<i>Thu</i></p><p class="day">01<i>Wed</i></p>
<p class="day">01<i>Wed</i></p><p class="day">02<i>Thu</i></p><p class="day">01<i>Wed</i></p><p class="day weekend">02<i>Thu</i></p><p class="day weekend">01<i>Wed</i></p><p class="day">02<i>Thu</i></p><p class="day">01<i>Wed</i></p>
<p class="day">01<i>Wed</i></p><p class="day">02<i>Thu</i></p><p class="day">01<i>Wed</i></p><p class="day weekend">02<i>Thu</i></p><p class="day weekend">01<i>Wed</i></p><p class="day">02<i>Thu</i></p><p class="day">01<i>Wed</i></p>
<p class="day">01<i>Wed</i></p><p class="day">02<i>Thu</i></p><p class="day">01<i>Wed</i></p>
</section>

<section class="month sep"><h2>SEP</h2>
<p class="day weekend">01<i>Sat</i></p><p class="day weekend">02<i>Sun</i></p><p class="day">01<i>Sat</i></p><p class="day">02<i>Sun</i></p><p class="day">01<i>Sat</i></p><p class="day">02<i>Sun</i></p><p class="day">01<i>Sat</i></p>
<p class="day weekend">01<i>Sat</i></p><p class="day weekend">02<i>Sun</i></p><p class="day">01<i>Sat</i></p><p class="day">02<i>Sun</i></p><p class="day">01<i>Sat</i></p><p class="day">02<i>Sun</i></p><p class="day">01<i>Sat</i></p>
<p class="day weekend">01<i>Sat</i></p><p class="day weekend">02<i>Sun</i></p><p class="day">01<i>Sat</i></p><p class="day">02<i>Sun</i></p><p class="day">01<i>Sat</i></p><p class="day">02<i>Sun</i></p><p class="day">01<i>Sat</i></p>
<p class="day weekend">01<i>Sat</i></p><p class="day weekend">02<i>Sun</i></p><p class="day">01<i>Sat</i></p><p class="day">02<i>Sun</i></p><p class="day">01<i>Sat</i></p><p class="day">02<i>Sun</i></p><p class="day">01<i>Sat</i></p>
<p class="day weekend">01<i>Sat</i></p><p class="day weekend">02<i>Sun</i></p><p class="day">01<i>Sat</i></p>
</section>

<section class="month oct"><h2>OCT</h2>
<p class="day">01<i>Mon</i></p><p class="day">02<i>Tue</i></p><p class="day">01<i>Mon</i></p><p class="day">02<i>Tue</i></p><p class="day">01<i>Mon</i></p><p class="day weekend">02<i>Tue</i></p><p class="day weekend">01<i>Mon</i></p>
<p class="day">01<i>Mon</i></p><p class="day">02<i>Tue</i></p><p class="day">01<i>Mon</i></p><p class="day">02<i>Tue</i></p><p class="day">01<i>Mon</i></p><p class="day weekend">02<i>Tue</i></p><p class="day weekend">01<i>Mon</i></p>
<p class="day">01<i>Mon</i></p><p class="day">02<i>Tue</i></p><p class="day">01<i>Mon</i></p><p class="day">02<i>Tue</i></p><p class="day">01<i>Mon</i></p><p class="day weekend">02<i>Tue</i></p><p class="day weekend">01<i>Mon</i></p>
<p class="day">01<i>Mon</i></p><p class="day">02<i>Tue</i></p><p class="day">01<i>Mon</i></p><p class="day">02<i>Tue</i></p><p class="day">01<i>Mon</i></p><p class="day weekend">02<i>Tue</i></p><p class="day weekend">01<i>Mon</i></p>
<p class="day">01<i>Mon</i></p><p class="day">02<i>Tue</i></p><p class="day">01<i>Mon</i></p>
</section>

<section class="month nov"><h2>NOV</h2>
<p class="day">01<i>Thu</i></p><p class="day">02<i>Fri</i></p><p class="day weekend">01<i>Thu</i></p><p class="day weekend">02<i>Fri</i></p><p class="day">01<i>Thu</i></p><p class="day">02<i>Fri</i></p><p class="day">01<i>Thu</i></p>
<p class="day">01<i>Thu</i></p><p class="day">02<i>Fri</i></p><p class="day weekend">01<i>Thu</i></p><p class="day weekend">02<i>Fri</i></p><p class="day">01<i>Thu</i></p><p class="day">02<i>Fri</i></p><p class="day">01<i>Thu</i></p>
<p class="day">01<i>Thu</i></p><p class="day">02<i>Fri</i></p><p class="day weekend">01<i>Thu</i></p><p class="day weekend">02<i>Fri</i></p><p class="day">01<i>Thu</i></p><p class="day">02<i>Fri</i></p><p class="day">01<i>Thu</i></p>
<p class="day">01<i>Thu</i></p><p class="day">02<i>Fri</i></p><p class="day weekend">01<i>Thu</i></p><p class="day weekend">02<i>Fri</i></p><p class="day">01<i>Thu</i></p><p class="day">02<i>Fri</i></p><p class="day">01<i>Thu</i></p>
<p class="day">01<i>Thu</i></p><p class="day">02<i>Fri</i></p><p class="day weekend">01<i>Thu</i></p>
</section>

<section class="month dec"><h2>DEC</h2>
<p class="day weekend">01<i>Sat</i></p><p class="day weekend">02<i>Sun</i></p><p class="day">01<i>Sat</i></p><p class="day">02<i>Sun</i></p><p class="day">01<i>Sat</i></p><p class="day">02<i>Sun</i></p><p class="day">01<i>Sat</i></p>
<p class="day weekend">01<i>Sat</i></p><p class="day weekend">02<i>Sun</i></p><p class="day">01<i>Sat</i></p><p class="day">02<i>Sun</i></p><p class="day">01<i>Sat</i></p><p class="day">02<i>Sun</i></p><p class="day">01<i>Sat</i></p>
<p class="day weekend">01<i>Sat</i></p><p class="day weekend">02<i>Sun</i></p><p class="day">01<i>Sat</i></p><p class="day">02<i>Sun</i></p><p class="day">01<i>Sat</i></p><p class="day">02<i>Sun</i></p><p class="day">01<i>Sat</i></p>
<p class="day weekend">01<i>Sat</i></p><p class="day weekend">02<i>Sun</i></p><p class="day">01<i>Sat</i></p><p class="day">02<i>Sun</i></p><p class="day">01<i>Sat</i></p><p class="day">02<i>Sun</i></p><p class="day">01<i>Sat</i></p>
<p class="day weekend">01<i>Sat</i></p><p class="day weekend">02<i>Sun</i></p><p class="day">01<i>Sat</i></p>
</section>

</div>
<h1 class="title">XYZ CO 2012 PLANNER</h1>
</main>
</body>
</html>
```